IT consulting company looking for a modern business design for a website and a new logo

We are the IT-consulting company VelmaTrix from Germany and need a new and modern business website and a new logo. We are specialized in output management. Our services include business analysis, outsourcing, development, training and project leading. We wish for a design with nature pictures (mountains, lakes, rivers, forests, etc.) for our company with the colors green and blue. If it is possible, a slow-mo video of a nature scene. The design should be responsive and the menu should change to a hamburger menu. The following are: • Services / Solutions 1. Output Management 2. Outsourcing 3. Development 4. Business Analyst 5. Training • Partners • Careers • About Us 1. Project A 2. Project B 3. Project C • Contact Notes for the following categories: For "Services / Solutions" we want to conclude some contents from all the sub-points and sub-points below. Additionally, we would like to see some sub-point under "Services / Solutions". For Output Management: "5 Benefits of Output Management Systems (OMS) - OMS Simplifies and Accelerates External Communication - Helps Reduce Communication Mistakes - Provides Customers With Fast and Secure Responses to your questions - Employees can focus on the essential as they can access prepared templates - Companies get complete transparency about their communication "The point" partner does not have sub-points. The content here is a quote and the logo from the company Brel. For now, just placeholders on this site. The next point wants to be "career" without sub-point and wants to contain some text. Carrer options wants to be listed here. Next point wants to be "About us", where we need sub-points which we do not know exactly at this moment, but they will contain text. By clicking directly on "About us" we want to include pictures and texts about 6 employees for which we only need placeholders at the moment. The last point wants to be "contact", where customers can send us messages. The main page should include a story about our company, which can be a placeholder for now. For reference, designs have a look at: https://brelvanto.de/ https://www.tarnopix.com/ https://www.pldrive.de/ We prefer WordPress designs, created with the plugin ELEMENTOR, so that we can easily edit the content by ourselves. The final design should look professional, competent and modern.

Target Market(s)

With our website, we want to reach the following target groups. <br> <br> <br> <br> <br> <br> <br> <br> <br> <br> <br> <br> <br> <br> <br> <br> <br> <br> <br> <br> <br> <br> <br> <br> <br> <br> <br> <br> <br> <br> <br> <br> <br> <br> <br> <br> <br> <br> <br> <br> <br> <br> <br> <br> <br> <br> <br> <br> <br>

Industry/Entity Type

Consulting

Logo Text

(optionally) VelmaTrix

Font styles to use
Sans Serif

Colors

Designer to choose colors to be used in the design.

Requirements
Must have
• 1. Outsourcing 3. Development 4. Business Analyst 5. Training • Partners • Careers • About Us 1. Project A 2. Project B 3. Project C • Contact The above-mentioned background picture with nature motifs (mountains, lakes, rivers, forests, etc.). WordPress design in primary colors blue and green.
Nice to have
• ELEMENTOR template. Effects for the background pictures. Counter of all successful projects for Output Management, Business Analyst and Training

```html
<!DOCTYPE html>
<html lang="de">
<head>
<meta charset="utf-8">
<title>VelmaTrix – IT Consulting</title>
<link href="https://fonts.googleapis.com/css2?family=Barlow:wght@400;500;600;700&family=Poppins:wght@400;500&display=swap" rel="stylesheet">
<style>
:root{
  --blue:#2e8fe6;
  --blue-light:#3a9cf0;
  --blue-deep:#1d4f8f;
  --ink:#222;
  --text:#555;
  --muted:#777;
  --grey-bg:#efefef;
  --beige:#f4f1e3;
  --white:#fff;
  --dark-btn:#222;
}
*{margin:0;padding:0;box-sizing:border-box}
html,body{width:1200px;height:4640px;overflow:hidden}
body{position:relative;font-family:'Poppins',sans-serif;color:var(--text);background:var(--white)}
.abs{position:absolute}
h1,h2,h3,.nav a,.logo,.btn{font-family:'Barlow',sans-serif}

/* hero */
.hero{left:0;top:0;width:1200px;height:659px;background:linear-gradient(180deg,#aebfcf 0%,#8aa0b0 18%,#4f7a52 45%,#6f9a3a 70%,#9bb544 100%)}
.logo{left:144px;top:40px;font-size:46px;font-weight:500;color:var(--ink);letter-spacing:-0.5px}
.nav{left:468px;top:57px;display:flex;gap:34px}
.nav a{font-size:16px;font-weight:600;color:var(--ink);text-decoration:none;letter-spacing:.3px}
.hero-title{left:0;width:1200px;top:340px;text-align:center;font-size:58px;font-weight:700;color:var(--white);text-shadow:0 2px 6px rgba(0,0,0,.35)}
.notch{left:559px;top:625px}

/* services */
.services{left:0;top:659px;width:1200px;height:889px;background:var(--grey-bg)}
.sec-title{font-size:38px;color:var(--ink);font-weight:400}
.sec-title b{font-weight:700}
.underline{height:4px;width:86px;background:var(--blue)}
.intro{font-size:13.5px;line-height:32px;color:var(--text)}
.card{width:434px;height:201px;background:var(--white);box-shadow:0 6px 14px rgba(0,0,0,.12)}
.card h3{position:absolute;top:30px;font-size:19px;font-weight:600;color:var(--ink)}
.card p{position:absolute;top:68px;width:250px;font-size:13px;line-height:26px;color:var(--text)}
.card svg{position:absolute;top:26px}
.card.right h3,.card.right p{left:140px}
.card.right svg{left:26px}
.card.left h3,.card.left p{right:140px;text-align:right}
.card.left svg{right:26px}

/* partner */
.partner{left:0;top:1548px;width:1200px;height:553px;background:linear-gradient(135deg,#3596ea,#2b86dc 55%,#3a9cf0)}
.partner .sec-title{color:var(--white);width:1200px;text-align:center;top:1640px}
.partner-intro{left:240px;width:720px;top:1740px;text-align:center;color:#e8f2fd;font-size:13.5px;line-height:32px}
.quote-card{left:252px;top:1885px;width:700px;height:270px;background:var(--white);border-radius:10px;box-shadow:0 8px 20px rgba(0,0,0,.15)}
.quote-name{left:252px;width:700px;top:1945px;text-align:center;color:var(--blue);font-size:17px}
.quote-text{left:300px;width:604px;top:1980px;text-align:center;font-style:italic;font-size:13px;line-height:27px;color:var(--text)}
.partner-name{top:2086px;font-family:'Barlow',sans-serif;font-size:26px;color:#666;font-weight:500}

/* career */
.career-art{left:117px;top:2268px;width:437px;height:405px;background:radial-gradient(ellipse at 55% 45%,#dbe6f5 0%,#eef2f8 55%,#fff 80%);border-radius:12px}
.career h2,.about-box h2{font-size:36px;font-weight:700;color:var(--ink)}
.checklist{list-style:none;font-size:12.5px;color:var(--ink)}
.checklist li{display:flex;align-items:center;gap:14px;height:29px}
.btn-outline{display:inline-block;border:2px solid var(--blue);color:var(--blue);font-size:14px;font-weight:600;text-align:center}

/* about */
.about{left:0;top:2795px;width:1200px;height:742px;background:linear-gradient(135deg,#1d4f8f,#2a5fa3 50%,#1c4886)}
.about-photo{left:520px;top:2925px;width:555px;height:482px;background:#fff;padding:4px}
.about-photo div{width:100%;height:100%;background:linear-gradient(135deg,#e9f1f7 0%,#9fc4dc 45%,#3f87b8 70%,#6a8fa8 100%)}
.about-box{left:164px;top:2975px;width:457px;height:378px;background:var(--white)}

/* info bar */
.infobar{left:0;top:3537px;width:1200px;height:175px;background:var(--blue-light)}
.info{top:3603px;display:flex;gap:20px;align-items:center;color:var(--white)}
.info strong{display:block;font-family:'Barlow',sans-serif;font-size:17px;font-weight:600}
.info span{font-size:15px}

/* contact */
.contact{left:0;top:3712px;width:1200px;height:640px;background:var(--beige)}
.field{left:164px;width:425px;height:38px;background:var(--white);border:1px solid #cfcbb8;font-size:12px;color:#444;padding:11px 14px}
.message{left:612px;top:3929px;width:423px;height:204px;background:var(--white);border:1px solid #cfcbb8;font-size:12px;color:#444;padding:14px}
.submit{left:495px;top:4185px;width:209px;height:49px;background:var(--dark-btn);color:var(--white);font-size:21px;font-weight:600;display:flex;align-items:center;justify-content:center;border-radius:3px}

/* footer */
.footer-links{left:0;width:1200px;top:4418px;text-align:center;font-size:16px;color:var(--ink)}
.copyright{left:0;width:1200px;top:4468px;text-align:center;font-size:16px;color:var(--ink)}
.social{left:533px;top:4529px;display:flex;gap:13px}
.social span{width:36px;height:36px;border:1.5px solid var(--ink);border-radius:50%}
</style>
</head>
<body>

<!-- Hero -->
<div class="abs hero" role="img" aria-label="Mountain valley with green slopes and a winding path under a cloudy sky"></div>
<div class="abs logo">VelmaTrix</div>
<nav class="abs nav"><a>HOME</a><a>SERVICES</a><a>PARTNER</a><a>KARRIERE</a><a>ÜBER UNS</a><a>KONTAKT</a></nav>
<svg class="abs" style="left:578px;top:262px" width="62" height="62" viewBox="0 0 62 62"><circle cx="31" cy="31" r="29" fill="none" stroke="#fff" stroke-width="2"/><path d="M25 19 L43 31 L25 43 Z" fill="none" stroke="#fff" stroke-width="2"/></svg>
<svg class="abs" style="left:98px;top:322px" width="34" height="34"><circle cx="17" cy="17" r="15" fill="rgba(0,0,0,.55)"/><path d="M20 10 L13 17 L20 24" stroke="#fff" stroke-width="2.5" fill="none"/></svg>
<svg class="abs" style="left:1067px;top:322px" width="34" height="34"><circle cx="17" cy="17" r="15" fill="rgba(0,0,0,.55)"/><path d="M14 10 L21 17 L14 24" stroke="#fff" stroke-width="2.5" fill="none"/></svg>
<h1 class="abs hero-title">VELMATRIX IT CONSULTING</h1>
<svg class="abs notch" width="82" height="36" viewBox="0 0 82 36"><path d="M0 36 Q25 36 35 8 Q41 -4 47 8 Q57 36 82 36 Z" fill="#efefef"/></svg>

<!-- Services -->
<section class="abs services"></section>
<h2 class="abs sec-title" style="left:144px;top:766px"><b>OUR</b> SERVICES</h2>
<div class="abs underline" style="left:144px;top:833px"></div>
<p class="abs intro" style="left:144px;top:858px;width:430px">Sed ut perspiciatis unde omnis iste natus error sit voluptatem accusantium doloremque laudantium, totam rem aperiam, eaque ipsa quae ab illo inventore veritatis et quasi</p>

<div class="abs card right" style="left:619px;top:760px">
  <svg width="90" height="90" viewBox="0 0 90 90"><circle cx="45" cy="45" r="42" fill="none" stroke="var(--blue)" stroke-width="2.5"/><rect x="27" y="30" width="34" height="26" fill="none" stroke="var(--blue)" stroke-width="2"/><circle cx="53" cy="50" r="7" fill="none" stroke="var(--blue)" stroke-width="2"/><path d="M58 55 L64 61" stroke="var(--blue)" stroke-width="2"/></svg>
  <h3>OUTPUT MANAGEMENT</h3>
  <p>Sed ut perspiciatis unde omnis iste natus error sit voluptatem accusantium doloremque laudantium, totam rem aperiam, eaque ipsa quae ab illo</p>
</div>
<div class="abs card left" style="left:144px;top:992px">
  <svg width="90" height="90" viewBox="0 0 90 90"><circle cx="45" cy="45" r="42" fill="none" stroke="var(--blue)" stroke-width="2.5"/><circle cx="45" cy="36" r="7" fill="none" stroke="var(--blue)" stroke-width="2"/><circle cx="31" cy="48" r="6" fill="none" stroke="var(--blue)" stroke-width="2"/><circle cx="59" cy="48" r="6" fill="none" stroke="var(--blue)" stroke-width="2"/><path d="M22 64 Q31 54 40 64 M50 64 Q59 54 68 64 M36 54 Q45 44 54 54" fill="none" stroke="var(--blue)" stroke-width="2"/></svg>
  <h3>OUTSOURCING</h3>
  <p>Sed ut perspiciatis unde omnis iste natus error sit voluptatem accusantium doloremque laudantium, totam rem aperiam, eaque ipsa quae ab illo</p>
</div>
<div class="abs card right" style="left:619px;top:992px">
  <svg width="90" height="90" viewBox="0 0 90 90"><circle cx="45" cy="45" r="42" fill="none" stroke="var(--blue)" stroke-width="2.5"/><rect x="26" y="28" width="38" height="28" rx="2" fill="none" stroke="var(--blue)" stroke-width="2"/><path d="M40 38 L36 42 L40 46 M50 38 L54 42 L50 46 M22 62 H68" fill="none" stroke="var(--blue)" stroke-width="2"/></svg>
  <h3>ENTWICKLUNG</h3>
  <p>Sed ut perspiciatis unde omnis iste natus error sit voluptatem accusantium doloremque laudantium, totam rem aperiam, eaque ipsa quae ab illo</p>
</div>
<div class="abs card left" style="left:144px;top:1224px">
  <svg width="90" height="90" viewBox="0 0 90 90"><circle cx="45" cy="45" r="42" fill="none" stroke="var(--blue)" stroke-width="2.5"/><rect x="40" y="24" width="26" height="20" fill="none" stroke="var(--blue)" stroke-width="2"/><path d="M45 40 V34 M51 40 V30 M57 40 V36" stroke="var(--blue)" stroke-width="2"/><circle cx="32" cy="44" r="6" fill="none" stroke="var(--blue)" stroke-width="2"/><path d="M22 66 Q32 50 42 66" fill="none" stroke="var(--blue)" stroke-width="2"/></svg>
  <h3>BUSINESS ANALYST</h3>
  <p>Sed ut perspiciatis unde omnis iste natus error sit voluptatem accusantium doloremque laudantium, totam rem aperiam, eaque ipsa quae ab illo</p>
</div>
<div class="abs card right" style="left:619px;top:1224px">
  <svg width="90" height="90" viewBox="0 0 90 90"><circle cx="45" cy="45" r="42" fill="none" stroke="var(--blue)" stroke-width="2.5"/><rect x="26" y="26" width="38" height="26" fill="none" stroke="var(--blue)" stroke-width="2"/><path d="M45 52 V58 M36 66 L45 58 L54 66 M32 44 L40 36 L48 42 L58 32" fill="none" stroke="var(--blue)" stroke-width="2"/></svg>
  <h3>SCHULUNGEN</h3>
  <p>Sed ut perspiciatis unde omnis iste natus error sit voluptatem accusantium doloremque laudantium, totam rem aperiam, eaque ipsa quae ab illo</p>
</div>

<!-- Partner -->
<section class="abs partner"></section>
<h2 class="abs sec-title partner-title" style="left:0;top:1640px;width:1200px;text-align:center;color:#fff"><b>OUR</b> PARTNER</h2>
<div class="abs underline" style="left:557px;top:1690px;background:#fff"></div>
<p class="abs partner-intro">Sed ut perspiciatis unde omnis iste natus error sit voluptatem accusantium doloremque laudantium, totam rem aperiam, eaque ipsa quae ab illo inventore veritatis et quasi</p>
<svg class="abs" style="left:184px;top:1990px" width="30" height="46"><path d="M24 4 L6 23 L24 42" stroke="#fff" stroke-width="2" fill="none"/></svg>
<svg class="abs" style="left:994px;top:1990px" width="30" height="46"><path d="M6 4 L24 23 L6 42" stroke="#fff" stroke-width="2" fill="none"/></svg>
<div class="abs quote-card"></div>
<svg class="abs" style="left:554px;top:1840px" width="90" height="90" viewBox="0 0 90 90"><circle cx="45" cy="45" r="43" fill="#fff" stroke="#ddd"/><circle cx="45" cy="45" r="36" fill="#eef1f5"/></svg>
<div class="abs quote-name">Jonas Weller</div>
<svg class="abs" style="left:286px;top:1982px" width="18" height="14"><text x="0" y="14" font-family="Georgia,serif" font-size="22" font-weight="700" fill="#333">“</text></svg>
<p class="abs quote-text">Nemo enim ipsam voluptatem quia voluptas sit aspernatur aut odit aut fugit, sed quia consequuntur magni dolores eos qui ratione voluptatem sequi nesciunt. Neque porro quisquam est, qui dolorem ipsum quia dolor sit amet, consectetur, adipisci velit, sed quia non numquam</p>
<svg class="abs" style="left:878px;top:2036px" width="18" height="14"><text x="0" y="18" font-family="Georgia,serif" font-size="22" font-weight="700" fill="#333">”</text></svg>
<div class="abs partner-name" style="left:482px">Norvik</div>
<div class="abs partner-name" style="left:617px">Lumera</div>

<!-- Career -->
<div class="abs career-art" role="img" aria-label="Illustration of a team meeting at a table in front of a large dashboard screen"></div>
<div class="career">
  <h2 class="abs" style="left:619px;top:2272px">KARRIERE</h2>
  <div class="abs underline" style="left:619px;top:2335px;width:80px"></div>
  <p class="abs intro" style="left:619px;top:2364px;width:470px;font-size:13.5px;line-height:29px">Sed ut perspiciatis unde omnis iste natus error sit voluptatem atium doloremque laudantium, totam rem aperiam, eaque ipsa quae ab illo inventore veritatis et quasi architecto beatae vitae dicta sunt explicabo. Nemo enim ipsam voluptatem</p>
  <ul class="abs checklist" style="left:619px;top:2493px">
    <li><svg width="14" height="14"><circle cx="7" cy="7" r="6" fill="none" stroke="var(--blue)" stroke-width="1.5"/><path d="M4 7 H10 M7 4 V10" stroke="var(--blue)" stroke-width="1.5"/></svg>Lorem ipsum dolor sit amet, consectetur</li>
    <li><svg width="14" height="14"><circle cx="7" cy="7" r="6" fill="none" stroke="var(--blue)" stroke-width="1.5"/><path d="M4 7 H10 M7 4 V10" stroke="var(--blue)" stroke-width="1.5"/></svg>Donec ultricies diam quis quam lobortis, vitae</li>
    <li><svg width="14" height="14"><circle cx="7" cy="7" r="6" fill="none" stroke="var(--blue)" stroke-width="1.5"/><path d="M4 7 H10 M7 4 V10" stroke="var(--blue)" stroke-width="1.5"/></svg>Cras porttitor ligula quis sapien eleifend ullamcorper.</li>
  </ul>
  <div class="abs btn btn-outline" style="left:619px;top:2606px;width:153px;height:42px;line-height:38px">APPLY NOW</div>
</div>

<!-- About -->
<section class="abs about" role="img" aria-label="Dimmed blue-toned photo of people working in an office"></section>
<div class="abs about-photo" role="img" aria-label="Photo of two colleagues working together at a laptop"><div></div></div>
<div class="abs about-box">
  <h2 class="abs" style="left:32px;top:50px">ÜBER UNS</h2>
  <p class="abs intro" style="left:32px;top:124px;width:400px;font-size:13.5px;line-height:32px">Sed ut perspiciatis unde omnis iste natus error sit voluptatem accntium doloremque laudantium, totam rem aperiam, eaque ipsa quae ab illo itore veritatis et quasi architecto beatae vitae dicta sunt explicabo. Nemo enim ipsam voluptatem quia voluptas sit aspernatur</p>
  <div class="abs btn btn-outline" style="left:32px;top:301px;width:142px;height:37px;line-height:33px">LEARN MORE</div>
</div>

<!-- Info bar -->
<div class="abs infobar"></div>
<div class="abs info" style="left:148px">
  <svg width="46" height="46"><circle cx="23" cy="23" r="21" fill="none" stroke="#fff" stroke-width="2"/><path d="M23 33 C16 24 16 21 16 19 A7 7 0 0 1 30 19 C30 21 30 24 23 33 Z" fill="none" stroke="#fff" stroke-width="2"/><circle cx="23" cy="19" r="2.5" fill="#fff"/></svg>
  <div><strong>Address:</strong><span>14 Talweg Strasse, Lindenau</span></div>
</div>
<div class="abs info" style="left:524px">
  <svg width="46" height="46"><circle cx="23" cy="23" r="21" fill="none" stroke="#fff" stroke-width="2"/><path d="M16 14 L20 13 L23 19 L20 21 Q22 26 26 28 L28 25 L34 28 L33 32 Q24 34 16 24 Q13 18 16 14 Z" fill="none" stroke="#fff" stroke-width="1.8"/></svg>
  <div><strong>Phone:</strong><span>(040) 5521 7730</span></div>
</div>
<div class="abs info" style="left:800px">
  <svg width="46" height="46"><circle cx="23" cy="23" r="21" fill="none" stroke="#fff" stroke-width="2"/><rect x="14" y="17" width="18" height="13" fill="none" stroke="#fff" stroke-width="1.8"/><path d="M14 17 L23 25 L32 17" fill="none" stroke="#fff" stroke-width="1.8"/></svg>
  <div><strong>Email:</strong><span>info@velmatrix.com</span></div>
</div>

<!-- Contact -->
<section class="abs contact" role="img" aria-label="Faint city skyline pattern on a light beige background"></section>
<h2 class="abs sec-title" style="left:0;width:1200px;text-align:center;top:3785px"><b>KONTAKT</b></h2>
<div class="abs underline" style="left:567px;top:3855px;width:66px"></div>
<div class="abs field" style="top:3929px">Name *</div>
<div class="abs field" style="top:3985px">Phone *</div>
<div class="abs field" style="top:4039px">Email *</div>
<div class="abs field" style="top:4095px">Subject *</div>
<div class="abs message">Message</div>
<div class="abs btn submit">SUBMIT</div>

<!-- Footer -->
<div class="abs footer-links">Home | Services | Partner | Karriere | Über uns | Kontakt</div>
<div class="abs copyright">VelmaTrix © 2019 All Rights Reserved | Privacy Policy</div>
<div class="abs social"><span></span><span></span><span></span></div>

</body>
</html>
```